Velkora Land Surveying Website Design

We are working with Velkora. They are a national land surveying company and in need of a new website design.

Some sites to use for inspiration:

https://brannickeng.com
https://www.dvwinc.com
https://kelvarin.com
https://gto.us
https://ravendobuilt.com
https://www.marbeckquillondale.com

Thank you for taking the time to consider designing a website for us. We are web developers based in Stockton and Los Angeles, CA, USA. Most of our projects go through the same process. Understanding this process may help you win a project with us. We custom-code all of our websites in-house. We don’t have any requirements as to what tools you use for your design, but we prefer Figma files. For any design that we label as four-stars, we send it to the client for review. The client picks the final design they want us to use. Once we complete this process, we will continue to show additional clients all the four-star sites and purchase them later. Your designs will have multiple chances to sell. For better chances of success, we ask that you follow these guidelines.

IMAGES:
If you use any images or icons in the design, we ask that you have a link to the asset so we can purchase the image/icon. Most of the designs we submit do not have the customer’s images on them unless they have some great images. Be creative; show us the feeling you are trying to portray with your image choices. Use any royalty-free site you choose. We subscribe to Pellix and mainly use their images, but we can purchase images outside of Pellix.

PLEASE NOTE: we will not submit designs to clients with watermarks on the images.

FONTS:
We ask that you identify the fonts used in the design. This can be done in a message if you want. We typically use Google Fonts and Pellix Fonts.

CONTENT:
We're always open to different content and ideas. We often submit designs with stock images so the client can see our vision. We typically take pictures after the website launch to use their images with our vision. Lorem Ipsum is fine for paragraphs, but we ask that you write the headers in correct English. We want to be able to show the vision and identify the sections of the website.

INSPIRATION:
We typically add a couple of links in the brief of websites we like to help you get started in your design.

REVISIONS:
We do not often ask for revisions of the designs unless we see something in the design that may not appeal to the client. If there are slight changes that we want to make, we do that in the development process.

FEEDBACK:
We rarely give feedback on designs during the design process. We are working on many website projects and do not have the time to provide feedback. We usually respond if your request is well thought out and asks specific questions, but a note asking “feedback, please” usually goes unanswered.

```html
<!DOCTYPE html>
<html lang="en">
<head>
<meta charset="utf-8">
<title>Velkora Land Surveying</title>
<link rel="stylesheet" href="https://fonts.googleapis.com/css2?family=Oswald:wght@600;700&family=Roboto:wght@400;500;700&family=Arimo:wght@400;700&display=swap">
<style>
:root{
  --red:#d3161b;
  --red-dark:#a80f13;
  --ink:#1b1b1b;
  --text:#555a60;
  --muted:#8a8f95;
  --line:#e6e7ea;
  --white:#ffffff;
  --black:#0c0c0c;
  --star:#f0a81c;
}
*{box-sizing:border-box;margin:0;padding:0}
html,body{width:1200px;height:5195px;overflow:hidden}
body{position:relative;font-family:"Arimo",Arial,sans-serif;color:var(--text);background:var(--white)}
.abs{position:absolute}
.heading{font-family:"Oswald",sans-serif;font-weight:700;text-transform:uppercase;color:var(--ink);letter-spacing:-.5px;line-height:1.15}
.btn{display:inline-flex;align-items:center;gap:12px;background:var(--red);color:var(--white);font:700 13px "Roboto",sans-serif;text-transform:uppercase;padding:0 10px 0 16px;height:38px}
.btn .arr{width:22px;height:22px;background:var(--white);display:flex;align-items:center;justify-content:center}
.photo{position:absolute}

/* header */
.hero{left:0;top:0;width:1200px;height:678px;background:linear-gradient(100deg,#3a2a1c 0%,#6b5434 30%,#9b8250 55%,#b68a4a 80%,#c56a3a 100%)}
.hero-sky{left:0;top:0;width:1200px;height:220px;background:linear-gradient(180deg,#d9c7a0 0%,#b89a62 100%);opacity:.55}
.hero-field{left:0;top:330px;width:1200px;height:348px;background:linear-gradient(180deg,rgba(80,110,40,.55),rgba(60,70,30,.75))}
.navbar{left:111px;top:24px;width:978px;height:71px;background:var(--white);display:flex;align-items:center;padding:0 18px}
.brand{display:flex;align-items:center;gap:10px}
.brand-mark{width:44px;height:44px;border-radius:50%;background:var(--red)}
.brand-name{font:700 19px "Roboto",sans-serif;color:var(--red);line-height:1.1;width:140px}
.menu{display:flex;align-items:center;margin-left:110px;font:500 15px "Roboto",sans-serif;color:var(--ink);text-transform:uppercase}
.menu a{color:inherit;text-decoration:none;position:relative}
.menu .sep{color:#9a9a9a;margin:0 19px;font-weight:400}
.menu .active::before{content:"";position:absolute;left:-4px;right:-4px;top:-30px;height:4px;background:var(--red)}
.search{margin-left:38px}
.hero-title{left:623px;top:254px;font-size:44px;color:var(--white);width:520px;line-height:1.15}
.hero-copy{left:623px;top:367px;width:470px;font-size:16px;line-height:26px;color:var(--white)}
.hero-btn{left:623px;top:433px}
.scroll{left:578px;top:583px;width:44px;height:44px;border-radius:50%;background:var(--white);display:flex;align-items:center;justify-content:center}

/* about */
.about-frame{left:313px;top:787px;width:377px;height:585px;border:4px solid var(--red)}
.about-photo{left:111px;top:875px;width:383px;height:408px;background:linear-gradient(180deg,#8fb0d6 0%,#c9d7e4 45%,#7a7a6a 70%,#5b5b52 100%)}
.about-card{left:536px;top:835px;width:565px;height:484px;background:var(--white);border:12px solid #f1f2f5;padding:42px 44px}
.about-card h2{font-size:44px;margin-bottom:12px}
.about-card p{font-size:15px;line-height:24px;text-align:justify;margin-bottom:24px}
.about-card .btn{margin-top:0}

/* services */
.services{left:0;top:1492px;width:1200px;height:1241px;overflow:hidden}
.services-bg{left:0;top:0;width:1200px;height:1000px;background:linear-gradient(180deg,#5a5b5c 0%,#76787a 35%,#8d8f91 60%,#6a6b6d 100%)}
.services-title{left:0;top:118px;width:1200px;text-align:center;color:var(--white);font-size:42px}
.svc{width:309px;height:442px;background:var(--white);box-shadow:8px 8px 0 var(--red);padding:36px 32px}
.svc h3{font:500 21px "Roboto",sans-serif;color:var(--ink);margin:22px 0 20px}
.svc p{font-size:15px;line-height:24px}
.svc .go{width:26px;height:26px;background:var(--red);display:flex;align-items:center;justify-content:center;margin-top:24px}
.build-band{left:0;top:0;width:1200px;height:1241px}
.build-photo{left:60px;top:730px;width:430px;height:511px;background:linear-gradient(180deg,#b9a88a 0%,#8c6f4c 30%,#c9d33a 60%,#6d6a5a 100%)}
.build-title{left:571px;top:982px;font-size:44px;color:var(--white);line-height:1.18}
.build-btn{left:571px;top:1110px}

/* gallery */
.gallery-title{left:0;top:2832px;width:1200px;text-align:center;font-size:42px}
.tile{position:absolute}

/* clients */
.clients{left:0;top:3576px;width:1200px;height:625px;background:linear-gradient(180deg,#d11a1e 0%,#c3171b 55%,#a51317 100%)}
.clients-title{left:0;top:108px;width:1200px;text-align:center;color:var(--white);font-size:42px}
.clients-copy{left:270px;top:184px;width:660px;text-align:center;color:var(--white);font-size:15px;line-height:26px}
.quote{top:246px;width:474px;height:246px;background:var(--white);padding:30px 44px}
.stars{color:var(--star);font-size:16px;letter-spacing:6px}
.quote p{font-style:italic;font-size:15px;line-height:26px;text-align:justify;margin:12px 0 14px}
.who{display:flex;align-items:baseline;gap:12px}
.who b{font:700 19px "Roboto",sans-serif;color:var(--ink)}
.who span{font-size:14px;color:var(--ink)}
.qmark{position:absolute;right:40px;bottom:8px;font:700 88px/1 Georgia,serif;color:var(--red)}
.nav-dot{top:360px;width:32px;height:32px;border-radius:50%;background:var(--ink);display:flex;align-items:center;justify-content:center}

/* contact */
.contact-title{left:0;top:4300px;width:1200px;text-align:center;font-size:42px}
.field{border:2px solid #8a8a8a;background:rgba(255,255,255,.85);font:500 14px "Roboto",sans-serif;color:var(--ink);padding:0 16px;display:flex;align-items:center}
.field.msg{align-items:flex-start;padding-top:18px}
.submit{left:526px;top:4633px;width:148px;height:38px;background:var(--red);color:var(--white);font:700 13px "Roboto",sans-serif;display:flex;align-items:center;justify-content:center;text-transform:uppercase}

/* footer */
.footer{left:0;top:4800px;width:1200px;height:395px;background:var(--black);color:var(--white);font-family:"Roboto",sans-serif}
.fcol{top:88px}
.fcol h4{font:500 19px "Roboto",sans-serif;padding-bottom:10px;position:relative;margin-bottom:16px}
.fcol h4::after{content:"";position:absolute;left:0;bottom:0;width:22px;height:2px;background:var(--white)}
.fcol p,.fcol li{font-size:13px;line-height:26px;list-style:none}
.info{display:flex;align-items:flex-start;gap:14px;font-size:13px;line-height:26px;margin-bottom:20px}
.ico{width:30px;height:30px;border-radius:50%;background:var(--red);display:flex;align-items:center;justify-content:center;flex:none}
.socials{display:flex;gap:10px}
.socials span{width:38px;height:38px;border-radius:50%;border:1px solid var(--white)}
.socials .on{background:var(--red);border-color:var(--red)}
.frule{left:111px;top:313px;width:978px;height:1px;background:#333}
.copy{left:0;top:345px;width:1200px;text-align:center;font-size:15px}
</style>
</head>
<body>

<!-- header / hero -->
<section class="hero abs" role="img" aria-label="Surveyor operating a total station on a tripod in a sunlit field with houses and hills behind">
  <div class="hero-sky abs"></div>
  <div class="hero-field abs"></div>
</section>
<nav class="navbar abs">
  <div class="brand"><span class="brand-mark"></span><span class="brand-name">Velkora Land Surveying</span></div>
  <div class="menu">
    <a class="active">Home</a><span class="sep">|</span>
    <a>About Us</a><span class="sep">|</span>
    <a>Services</a><span class="sep">|</span>
    <a>Blog</a><span class="sep">|</span>
    <a>Gallery</a><span class="sep">|</span>
    <a>Contact</a>
    <svg class="search" width="16" height="16" viewBox="0 0 16 16"><circle cx="6.5" cy="6.5" r="4.8" fill="none" stroke="#1b1b1b" stroke-width="2"/><path d="M10 10l4 4" stroke="#1b1b1b" stroke-width="2.4" stroke-linecap="round"/></svg>
  </div>
</nav>
<h1 class="heading hero-title abs" style="color:#fff">Best Land Surveying &amp; Digital Mapping Services</h1>
<p class="hero-copy abs">Lorem ipsum dolor sit amet, consectetur adipiscing elit, sed do eiusmod tempor incididunt ut labore et dolore</p>
<a class="btn hero-btn abs">Learn More <span class="arr"><svg width="10" height="12" viewBox="0 0 10 12"><path d="M2 1l5 5-5 5" fill="none" stroke="#d3161b" stroke-width="2.4"/></svg></span></a>
<div class="scroll abs"><svg width="18" height="18" viewBox="0 0 18 18"><path d="M4 3l5 5 5-5M4 9l5 5 5-5" fill="none" stroke="#1b1b1b" stroke-width="2"/></svg></div>

<!-- about -->
<div class="about-frame abs"></div>
<div class="about-photo photo" role="img" aria-label="Surveyor in hard hat and orange vest working a theodolite beside a road"></div>
<article class="about-card abs">
  <h2 class="heading">About Us</h2>
  <p>Lorem ipsum dolor sit amet, consectetur adipiscing elit, sed do eiusmod tempor incididunt ut labore et dolore magna aliqua. Ut enim ad minim veniam, quis nostrud exercitation ullamco laboris nisi ut aliquip ex ea commodo consequat. Duis aute irure dolor in reprehenderit in voluptate velit esse cillum dolore eu fugiat nulla pariatur.</p>
  <p>Excepteur sint occaecat cupidatat non proident, sunt in culpa qui officia deserunt mollit anim id est laborum. Lorem ipsum dolor sit amet, consectetur adipiscing elit, sed do eiusmod tempor incididunt ut labore et dolore magna aliqua.</p>
  <a class="btn">Learn More <span class="arr"><svg width="10" height="12" viewBox="0 0 10 12"><path d="M2 1l5 5-5 5" fill="none" stroke="#d3161b" stroke-width="2.4"/></svg></span></a>
</article>

<!-- services -->
<section class="services abs">
  <div class="services-bg abs" role="img" aria-label="Greyscale surveying site with tripod equipment"></div>
  <svg class="build-band abs" width="1200" height="1241" viewBox="0 0 1200 1241">
    <polygon points="0,808 1200,902 1200,1241 0,1241" fill="#1d1d1d"/>
    <polygon points="0,796 1200,890 1200,902 0,808" fill="#ffffff"/>
  </svg>
  <div class="build-photo photo" role="img" aria-label="Surveyor in hard hat and hi-vis vest looking through a total station"></div>
  <h2 class="heading services-title abs" style="color:#fff">Our Services</h2>

  <article class="svc abs" style="left:111px;top:200px">
    <svg width="80" height="74" viewBox="0 0 80 74" fill="none" stroke="#d3161b" stroke-width="2.4"><rect x="6" y="20" width="44" height="50"/><path d="M14 8h28v12H14zM14 34h28M14 44h28M14 54h20"/><path d="M60 10v60M54 70h12M60 10l10 8"/></svg>
    <h3>Lorem ipsum dolor</h3>
    <p>Lorem ipsum dolor sit amet, con sectetur adipiscing elit, sed do eiusmod tempor incididunt ut lab ore et dolore magna aliqua. Ut enim ad minim veniam, quis nos trud exercitation ullamco laboris consequat.</p>
    <div class="go"><svg width="10" height="12" viewBox="0 0 10 12"><path d="M2 1l5 5-5 5" fill="none" stroke="#fff" stroke-width="2.4"/></svg></div>
  </article>
  <article class="svc abs" style="left:446px;top:235px">
    <svg width="80" height="74" viewBox="0 0 80 74" fill="none" stroke="#d3161b" stroke-width="2.4"><path d="M34 4h12v14H34zM40 18v22M34 40l6 10 6-10"/><rect x="4" y="44" width="72" height="12"/><path d="M4 56v14h72V56M10 70l8-14M24 70l8-14M38 70l8-14M52 70l8-14"/></svg>
    <h3>Lorem ipsum dolor</h3>
    <p>Lorem ipsum dolor sit amet, con sectetur adipiscing elit, sed do eiusmod tempor incididunt ut lab ore et dolore magna aliqua. Ut enim ad minim veniam, quis nos trud exercitation ullamco laboris consequat.</p>
    <div class="go"><svg width="10" height="12" viewBox="0 0 10 12"><path d="M2 1l5 5-5 5" fill="none" stroke="#fff" stroke-width="2.4"/></svg></div>
  </article>
  <article class="svc abs" style="left:781px;top:269px">
    <svg width="80" height="74" viewBox="0 0 80 74" fill="none" stroke="#d3161b" stroke-width="2.4"><rect x="8" y="8" width="46" height="62" rx="3"/><path d="M22 4h18v8H22zM16 26l4 4 6-8M30 28h16M16 42l4 4 6-8M30 44h16M16 58l4 4 6-8M30 60h10"/><path d="M66 20l8 8-22 22-10 2 2-10z"/></svg>
    <h3>Lorem ipsum dolor</h3>
    <p>Lorem ipsum dolor sit amet, con sectetur adipiscing elit, sed do eiusmod tempor incididunt ut lab ore et dolore magna aliqua. Ut enim ad minim veniam, quis nos trud exercitation ullamco laboris consequat.</p>
    <div class="go"><svg width="10" height="12" viewBox="0 0 10 12"><path d="M2 1l5 5-5 5" fill="none" stroke="#fff" stroke-width="2.4"/></svg></div>
  </article>

  <h2 class="heading build-title abs" style="color:#fff">We Help You To Build<br>Everything You Needed</h2>
  <a class="btn build-btn abs">Learn More <span class="arr"><svg width="10" height="12" viewBox="0 0 10 12"><path d="M2 1l5 5-5 5" fill="none" stroke="#d3161b" stroke-width="2.4"/></svg></span></a>
</section>

<!-- gallery -->
<h2 class="heading gallery-title abs">Our Gallery</h2>
<div class="tile" style="left:111px;top:2908px;width:478px;height:271px;background:linear-gradient(180deg,#8e9296 0%,#6c7a55 55%,#4e5a38 100%)" role="img" aria-label="Survey crew in hi-vis vests discussing plans on a rural road"></div>
<div class="tile" style="left:607px;top:2908px;width:230px;height:271px;background:linear-gradient(180deg,#3d4a2c 0%,#6a6a55 50%,#a0622a 100%)" role="img" aria-label="Close-up of a total station on a tripod"></div>
<div class="abs" style="left:698px;top:3019px;width:50px;height:50px;border-radius:50%;background:var(--red);display:flex;align-items:center;justify-content:center"><svg width="20" height="20" viewBox="0 0 20 20"><path d="M10 2v16M2 10h16" stroke="#fff" stroke-width="2"/></svg></div>
<div class="tile" style="left:857px;top:2908px;width:232px;height:271px;background:linear-gradient(180deg,#b8bcc0 0%,#c6c24a 50%,#a98a62 100%)" role="img" aria-label="Two surveyors in hard hats reviewing a site plan outdoors"></div>
<div class="tile" style="left:111px;top:3191px;width:232px;height:270px;background:linear-gradient(180deg,#37598a 0%,#8fa9c6 45%,#6b7d8c 100%)" role="img" aria-label="Yellow survey tripod under a cloudy sky"></div>
<div class="tile" style="left:361px;top:3191px;width:232px;height:270px;background:linear-gradient(180deg,#9aa6ad 0%,#e09a2a 45%,#c6d23a 100%)" role="img" aria-label="Surveyor in blue hard hat using an orange instrument"></div>
<div class="tile" style="left:611px;top:3191px;width:478px;height:270px;background:linear-gradient(180deg,#9da3a8 0%,#6d6659 55%,#4f4a42 100%)" role="img" aria-label="Survey team with instruments at an earthworks construction site"></div>

<!-- clients -->
<section class="clients abs" role="img" aria-label="Red-tinted field with surveyors in the background">
  <h2 class="heading clients-title abs" style="color:#fff">Happy Clients</h2>
  <p class="clients-copy abs">Lorem ipsum dolor sit amet, consectetur adipiscing elit, sed do eiusmod tempor incididunt ut labore et dolore magna aliqua. Ut enim ad minim veniam, quis</p>
  <article class="quote abs" style="left:111px">
    <div class="stars">★★★★★</div>
    <p>“Lorem ipsum dolor sit amet, consectetur adipiscing elit, sed do eiusmod tempor incididunt ut labore et dolore magna aliqua. Ut enim ad minim veniam, quis nostrud exercitation ullamco fugiat nulla pariatur.”</p>
    <div class="who"><b>John Doe</b><span>Company name</span></div>
    <span class="qmark">”</span>
  </article>
  <article class="quote abs" style="left:615px">
    <div class="stars">★★★★★</div>
    <p>“Lorem ipsum dolor sit amet, consectetur adipiscing elit, sed do eiusmod tempor incididunt ut labore et dolore magna aliqua. Ut enim ad minim veniam, quis nostrud exercitation ullamco fugiat nulla pariatur.”</p>
    <div class="who"><b>John Doe</b><span>Company name</span></div>
    <span class="qmark">”</span>
  </article>
  <div class="nav-dot abs" style="left:39px"><svg width="10" height="12" viewBox="0 0 10 12"><path d="M7 1L2 6l5 5" fill="none" stroke="#fff" stroke-width="2"/></svg></div>
  <div class="nav-dot abs" style="left:1128px"><svg width="10" height="12" viewBox="0 0 10 12"><path d="M3 1l5 5-5 5" fill="none" stroke="#fff" stroke-width="2"/></svg></div>
</section>

<!-- contact -->
<h2 class="heading contact-title abs">Contact Us</h2>
<div class="field abs" style="left:212px;top:4381px;width:236px;height:55px">Name</div>
<div class="field abs" style="left:476px;top:4381px;width:236px;height:55px">Email</div>
<div class="field abs" style="left:740px;top:4381px;width:236px;height:55px">Phone</div>
<div class="field msg abs" style="left:212px;top:4458px;width:764px;height:157px">Message</div>
<div class="submit abs">Submit Now</div>

<!-- footer -->
<footer class="footer abs">
  <div class="fcol abs" style="left:165px;width:230px">
    <h4>About Us</h4>
    <p>Lorem ipsum dolor sit amet, cons ect etur adipiscing elit, sed do eiusmod tempor incididunt</p>
  </div>
  <div class="fcol abs" style="left:450px">
    <h4>Sitemap</h4>
    <ul><li>Home</li><li>About</li><li>Services</li><li>Gallery</li><li>Blog</li><li>Contact</li></ul>
  </div>
  <div class="fcol abs" style="left:615px;width:230px">
    <h4>Contact info</h4>
    <div class="info"><span class="ico"><svg width="12" height="14" viewBox="0 0 12 14"><path d="M6 13S1 8 1 5a5 5 0 0110 0c0 3-5 8-5 8z" fill="#fff"/><circle cx="6" cy="5" r="1.8" fill="#d3161b"/></svg></span><span>123, Lorem ipsum dolor<br>sit amet</span></div>
    <div class="info"><span class="ico"><svg width="13" height="13" viewBox="0 0 13 13"><path d="M3 1l2 3-1.5 1.5a7 7 0 004 4L9 8l3 2-1.5 2C6 12 1 7 1 2.5z" fill="#fff"/></svg></span><span>+1 888 888 8888</span></div>
    <div class="info"><span class="ico"><svg width="14" height="10" viewBox="0 0 14 10"><rect x="0.5" y="0.5" width="13" height="9" fill="#fff"/><path d="M1 1l6 5 6-5" fill="none" stroke="#d3161b" stroke-width="1.2"/></svg></span><span>info@companyname.com</span></div>
  </div>
  <div class="fcol abs" style="left:881px">
    <h4>Social with us</h4>
    <div class="socials"><span></span><span class="on"></span><span></span></div>
  </div>
  <div class="frule abs"></div>
  <p class="copy abs">© Copyrights 2025 Company name | All Rights Reserved</p>
</footer>

</body>
</html>
```